Super elegant, crisp & clean Business card design required

We recently upgraded our branding - which is on our website - talvendoraphoto.com

I would like a simple, yet elegant, clean business card design please.

The font of my logo is Cinzel - and because of the natural colour - it's best to have this on a black background.

I would like to have the back of the business card - with simply my logo.

PLEASE DO NOT SUBMIT A COMPLICATED / UNCLEAN DESIGN

Industry/Entity Type

Business

Contact Information for Business Card

Talven Doroshko Photography

Font styles to use
Other font styles liked:
• Cinzel

Requirements
Must have
• A backpage with nothing but my logo
• Simple design - stands out
Should not have
• Colour that dont align with my logo
• Over complicated '/ non symmetrical design

```html
<!DOCTYPE html>
<html lang="en">
<head>
<meta charset="utf-8">
<title>Talven Doroshko Photography – Business Card</title>
<link rel="stylesheet" href="https://fonts.googleapis.com/css2?family=Cinzel:wght@400&family=Arimo:wght@400&display=swap">
<style>
  :root {
    --stage: #e9e7e3;
    --paper: #fbfbfa;
    --ink-dark: #1d1d1f;
    --panel-dark: #2a2a2c;
    --panel-dark-2: #121213;
    --taupe: #9c8e74;
    --taupe-light: #b3a78f;
    --text-grey: #3a3a3a;
  }
  * { box-sizing: border-box; margin: 0; padding: 0; }
  html, body { width: 1200px; height: 892px; overflow: hidden; }
  body {
    background: var(--stage);
    display: flex;
    align-items: center;
    justify-content: center;
    gap: 36px;
  }
  .card {
    width: 560px;
    height: 320px;
    position: relative;
    background: var(--paper);
    box-shadow: 0 6px 18px rgba(0,0,0,.18);
    overflow: hidden;
  }

  /* Back side: logo only */
  .card-back {
    display: flex;
    flex-direction: column;
    align-items: center;
    justify-content: center;
  }
  .brand-name {
    font-family: "Cinzel", serif;
    font-weight: 400;
    color: var(--taupe);
    text-align: center;
    line-height: 1.1;
  }
  .card-back .brand-name .name { font-size: 36px; display: block; }
  .card-back .brand-name .trade {
    font-size: 16px;
    letter-spacing: 0.62em;
    display: block;
    margin-top: 6px;
    margin-right: -0.62em;
  }

  /* Front side */
  .card-front { display: flex; }
  .edge-strip { width: 14px; background: var(--taupe); }
  .dark-panel {
    width: 238px;
    background: linear-gradient(160deg, var(--panel-dark) 0%, var(--panel-dark-2) 100%);
    display: flex;
    align-items: center;
    justify-content: center;
  }
  .dark-panel .brand-name .name { font-size: 17px; display: block; }
  .dark-panel .brand-name .trade {
    font-size: 9px;
    letter-spacing: 0.5em;
    display: block;
    margin-top: 4px;
    margin-right: -0.5em;
  }
  .icon-band {
    width: 34px;
    background: var(--taupe);
    position: relative;
  }
  .icon {
    position: absolute;
    left: 50%;
    transform: translate(-50%, -50%);
    display: block;
  }
  .icon-person { top: 62px; }
  .icon-phone { top: 164px; }
  .icon-email { top: 196px; }
  .icon-web { top: 228px; }

  .details {
    flex: 1;
    padding: 44px 0 0 26px;
    color: var(--text-grey);
  }
  .holder-name {
    font-family: "Cinzel", serif;
    font-size: 22px;
    color: var(--ink-dark);
    letter-spacing: 0.03em;
  }
  .holder-role {
    font-family: "Cinzel", serif;
    font-size: 11px;
    letter-spacing: 0.12em;
    margin-top: 2px;
  }
  .contact-list {
    list-style: none;
    margin-top: 60px;
    font-family: "Arimo", sans-serif;
    font-size: 15px;
    line-height: 32px;
  }
</style>
</head>
<body>

  <section class="card card-back" aria-label="Business card, back">
    <p class="brand-name">
      <span class="name">Talven Doroshko</span>
      <span class="trade">PHOTOGRAPHY</span>
    </p>
  </section>

  <section class="card card-front" aria-label="Business card, front">
    <div class="edge-strip"></div>
    <div class="dark-panel">
      <p class="brand-name">
        <span class="name">Talven Doroshko</span>
        <span class="trade">PHOTOGRAPHY</span>
      </p>
    </div>
    <div class="icon-band">
      <svg class="icon icon-person" width="28" height="28" viewBox="0 0 28 28" aria-hidden="true">
        <circle cx="14" cy="14" r="13" fill="#fbfbfa"/>
        <circle cx="14" cy="14" r="5" fill="#9c8e74"/>
      </svg>
      <svg class="icon icon-phone" width="18" height="18" viewBox="0 0 18 18" aria-hidden="true">
        <rect x="1" y="1" width="16" height="16" rx="3" fill="#fbfbfa"/>
        <rect x="6" y="3.5" width="6" height="11" rx="1.2" fill="#9c8e74"/>
        <circle cx="9" cy="12.6" r=".8" fill="#fbfbfa"/>
      </svg>
      <svg class="icon icon-email" width="18" height="18" viewBox="0 0 18 18" aria-hidden="true">
        <rect x="1" y="1" width="16" height="16" rx="3" fill="#fbfbfa"/>
        <rect x="4" y="5.5" width="10" height="7" fill="none" stroke="#9c8e74" stroke-width="1.3"/>
        <path d="M4 5.5 L9 9.5 L14 5.5" fill="none" stroke="#9c8e74" stroke-width="1.3"/>
      </svg>
      <svg class="icon icon-web" width="18" height="18" viewBox="0 0 18 18" aria-hidden="true">
        <rect x="1" y="1" width="16" height="16" rx="3" fill="#fbfbfa"/>
        <circle cx="9" cy="9" r="5" fill="none" stroke="#9c8e74" stroke-width="1.2"/>
        <ellipse cx="9" cy="9" rx="2.2" ry="5" fill="none" stroke="#9c8e74" stroke-width="1"/>
        <line x1="4" y1="9" x2="14" y2="9" stroke="#9c8e74" stroke-width="1"/>
      </svg>
    </div>
    <div class="details">
      <h1 class="holder-name">TALVEN DOROSHKO</h1>
      <p class="holder-role">OWNER</p>
      <ul class="contact-list">
        <li>07700900481</li>
        <li>info@talvendoraphoto.com</li>
        <li>www.talvendoraphoto.com</li>
      </ul>
    </div>
  </section>

</body>
</html>
```